Hollowbrook Anglican Church Christmas Advertising

We need a postcard design for our upcoming Christmas events in Dec 2013

This is an exciting time of year and we want to give lots people in the local community a chance to celebrate Christmas with us

Key events
Songs by the Green Sat 14th Dec 5.00pm Corliss Park, Tamber St, Hollowbrook (opp church)
Christmas Eve Family Service 6.30pm
Christmas Eve Lessons and Carols 8.30pm
Christmas Day Celebration Service 9.30am

We have a church logo to include. Outline of the church with 2 lines, one green and one yellow line.
The advertising should be fun, punchy and bright colours. Possibly use a line such as Christmas Unwrapped...Jesus is the best present. (this is just an idea)

```html
<!DOCTYPE html>
<html lang="en">
<head>
<meta charset="utf-8">
<title>Hollowbrook Anglican Church – Christmas Postcard</title>
<link rel="stylesheet" href="https://fonts.googleapis.com/css2?family=Kalam:wght@700&family=Open+Sans:wght@300;400&display=swap">
<style>
  :root {
    --page: #e6e6e6;
    --front-bg: #050505;
    --white: #ffffff;
    --gold: #e7a124;
    --silver: #8d8f91;
    --ink: #3a3a3a;
    --rule: #9a9a9a;
  }
  * { box-sizing: border-box; margin: 0; padding: 0; }
  html, body { width: 900px; height: 1200px; overflow: hidden; }
  body { background: var(--page); position: relative; font-family: "Open Sans", sans-serif; }

  .postcard { position: absolute; left: 135px; width: 630px; overflow: hidden; }
  .postcard--front { top: 83px; height: 483px; background: var(--front-bg); }
  .postcard--back { top: 638px; height: 484px; background: var(--white); }

  /* front */
  .tree-photo {
    position: absolute; right: 0; top: 0; width: 390px; height: 483px;
    background:
      radial-gradient(ellipse 55% 60% at 78% 55%, #4f8a3a 0%, #2c5a22 40%, rgba(10,20,8,0) 75%),
      radial-gradient(circle at 30% 30%, rgba(200,210,220,0.35) 0%, rgba(0,0,0,0) 30%),
      linear-gradient(90deg, #050505 0%, #0d1a0b 40%, #1c3515 100%);
  }
  .event-list { position: absolute; left: 30px; top: 32px; width: 440px; color: var(--white); font-family: "Kalam", cursive; font-weight: 700; }
  .event { margin-bottom: 24px; }
  .event__title { font-size: 26px; line-height: 33px; display: block; }
  .event__detail { font-size: 20px; line-height: 27px; display: block; }
  .front-band { position: absolute; left: 0; bottom: 0; width: 630px; height: 483px; }
  .front-name { position: absolute; right: 28px; bottom: 28px; color: var(--white); font-weight: 300; text-align: left; }
  .front-name__main { display: block; font-size: 33px; line-height: 36px; }
  .front-name__sub { display: block; font-size: 19px; line-height: 22px; }

  /* back */
  .back-name { position: absolute; left: 30px; top: 130px; color: var(--ink); font-weight: 300; }
  .back-name__main { display: block; font-size: 31px; line-height: 36px; }
  .back-name__sub { display: block; font-size: 19px; line-height: 24px; }
  .back-address { position: absolute; left: 27px; top: 283px; color: var(--ink); font-size: 17px; line-height: 22.5px; font-weight: 400; }
  .back-divider { position: absolute; left: 315px; top: 37px; width: 1px; height: 409px; background: var(--rule); }
  .stamp-box { position: absolute; left: 510px; top: 35px; width: 78px; height: 102px; border: 1px solid var(--rule); }
  .address-line { position: absolute; left: 348px; width: 246px; height: 1px; background: var(--rule); }
</style>
</head>
<body>

<section class="postcard postcard--front">
  <div class="tree-photo" role="img" aria-label="Photo of a clear glass angel ornament playing a horn, hanging before a lit green Christmas tree with soft bokeh lights"></div>

  <div class="event-list">
    <p class="event">
      <span class="event__title">Songs by the Green Sat</span>
      <span class="event__detail">14th Dec 5.00pm Corliss Park,</span>
      <span class="event__detail">Tamber St, Hollowbrook (opp church)</span>
    </p>
    <p class="event">
      <span class="event__title">Christmas Eve</span>
      <span class="event__title">Family Service 6.30pm</span>
    </p>
    <p class="event">
      <span class="event__title">Christmas Eve Lessons</span>
      <span class="event__title">&nbsp;and Carols 8.30pm</span>
    </p>
    <p class="event">
      <span class="event__title">Christmas Day Celebration</span>
      <span class="event__title">Service 9.30am</span>
    </p>
  </div>

  <svg class="front-band" viewBox="0 0 630 483" aria-hidden="true">
    <path d="M0 476 C 190 400, 400 356, 630 346 L630 365 C 400 374, 200 420, 0 483 Z" fill="var(--silver)"/>
    <path d="M0 483 C 200 420, 400 374, 630 365 L630 483 Z" fill="var(--gold)"/>
  </svg>

  <p class="front-name">
    <span class="front-name__main">Hollowbrook</span>
    <span class="front-name__sub">Anglican Church</span>
  </p>
</section>

<section class="postcard postcard--back">
  <p class="back-name">
    <span class="back-name__main">Hollowbrook</span>
    <span class="back-name__sub">Anglican Church</span>
  </p>

  <p class="back-address">
    Location:<br>
    Hollowbrook Anglican Church<br>
    Cnr Wrenfield and Tamber St,<br>
    Hollowbrook<br>
    Office: 02 5550 1742
  </p>

  <div class="back-divider"></div>
  <div class="stamp-box"></div>
  <div class="address-line" style="top:296px"></div>
  <div class="address-line" style="top:332px"></div>
  <div class="address-line" style="top:369px"></div>
  <div class="address-line" style="top:407px"></div>
</section>

</body>
</html>
```